Belmont Ridge Business Card Design Project

We have recently rebranded and would like to design new business cards that incorporate the corporate logo - double sided cards with corporate logo on one side and contact details on the other

Target Market(s)

Sophisticated and high net worth investors and finance industry professionals

Industry/Entity Type

Funds Management

Contact Information for Business Card

The card should prominently feature the company name and logo. Other details will be standard contact details for each staff member - name, address, phone, email, website

Colors
0054AA
0677BA
7BADD7
CADEEF
E8F1F8

Requirements
Must have
• Double-sided design with one side prominently featuring the corporate logo and the other side with all standard contact details

```html
<!DOCTYPE html>
<html lang="en">
<head>
<meta charset="utf-8">
<title>Belmont Ridge Business Card</title>
<link href="https://fonts.googleapis.com/css2?family=Arimo:wght@400;700&display=swap" rel="stylesheet">
<style>
  :root {
    --page-bg: #e9e9e8;
    --card-navy: #1f4677;
    --card-deep: #183a66;
    --accent-light: #4f86c6;
    --ink-white: #ffffff;
    --ink-soft: #e8f1f8;
  }
  html, body {
    margin: 0;
    padding: 0;
    width: 1200px;
    height: 802px;
    overflow: hidden;
    background: var(--page-bg);
    font-family: "Arimo", Arial, sans-serif;
  }
  .stage {
    position: relative;
    width: 1200px;
    height: 802px;
  }
  .card {
    position: absolute;
    top: 246px;
    width: 540px;
    height: 309px;
    border-radius: 3px;
    box-shadow: 0 10px 28px rgba(0,0,0,0.18);
    overflow: hidden;
    color: var(--ink-white);
  }
  .card--front {
    left: 40px;
    background: var(--card-navy);
  }
  .card--back {
    left: 620px;
  }

  /* Front side */
  .brand-name {
    position: absolute;
    top: 58px;
    left: 0;
    right: 0;
    text-align: center;
    font-weight: 700;
    font-size: 30px;
    letter-spacing: 2px;
    text-transform: uppercase;
    color: var(--ink-white);
  }
  .divider-long {
    position: absolute;
    top: 128px;
    left: 36px;
    right: 36px;
    height: 1px;
    background: var(--ink-soft);
  }
  .address {
    position: absolute;
    top: 146px;
    right: 40px;
    text-align: right;
    font-size: 13px;
    line-height: 17px;
    color: var(--ink-soft);
  }
  .person {
    position: absolute;
    left: 36px;
    top: 190px;
  }
  .person-name {
    font-weight: 700;
    font-size: 17px;
    letter-spacing: 0.3px;
    text-transform: uppercase;
  }
  .person-title {
    font-size: 13px;
    margin-top: 2px;
    color: var(--ink-soft);
  }
  .divider-short {
    width: 200px;
    height: 1px;
    background: var(--ink-soft);
    margin: 7px 0 8px;
  }
  .contact-list {
    list-style: none;
    margin: 0;
    padding: 0;
    font-size: 13.5px;
    line-height: 19px;
  }
  .contact-list li {
    display: flex;
    align-items: center;
    gap: 8px;
  }
  .contact-list svg {
    width: 11px;
    height: 11px;
    flex: none;
  }

  /* Back side */
  .back-pattern {
    position: absolute;
    inset: 0;
    background: linear-gradient(115deg, var(--card-deep) 0%, var(--card-navy) 55%, var(--accent-light) 100%);
  }
  .back-brand {
    position: absolute;
    top: 0;
    bottom: 0;
    left: 0;
    right: 0;
    display: flex;
    align-items: center;
    justify-content: center;
    gap: 12px;
    font-weight: 700;
    font-size: 30px;
    letter-spacing: 2px;
    text-transform: uppercase;
    color: var(--ink-white);
  }
  .back-brand .mark-square {
    width: 16px;
    height: 16px;
    background: var(--ink-white);
  }
</style>
</head>
<body>
<main class="stage">
  <section class="card card--front" aria-label="Business card front">
    <div class="brand-name">Belmont Ridge</div>
    <div class="divider-long"></div>
    <div class="address">Your Address, City<br>State, Zip 0000</div>
    <div class="person">
      <div class="person-name">Daniel Hartley</div>
      <div class="person-title">Manager</div>
      <div class="divider-short"></div>
      <ul class="contact-list">
        <li>
          <svg viewBox="0 0 12 12" aria-hidden="true"><circle cx="6" cy="6" r="6" fill="#fff"/><path d="M4 3.2l1 1.3-.6.7c.4.9 1 1.5 1.9 1.9l.7-.6 1.3 1-.6 1.2C5.6 8.5 3.5 6.4 3 3.8z" fill="#1f4677"/></svg>
          <span>555-014-2100</span>
        </li>
        <li>
          <svg viewBox="0 0 12 12" aria-hidden="true"><rect x="0.5" y="2" width="11" height="8" fill="#fff"/><path d="M0.5 2l5.5 4.5L11.5 2" fill="none" stroke="#1f4677" stroke-width="1"/></svg>
          <span>contact@belmontridge.com</span>
        </li>
        <li>
          <svg viewBox="0 0 12 12" aria-hidden="true"><circle cx="6" cy="6" r="6" fill="#fff"/><circle cx="6" cy="6" r="3.6" fill="none" stroke="#1f4677" stroke-width="0.9"/><path d="M2.4 6h7.2M6 2.4v7.2" stroke="#1f4677" stroke-width="0.9"/></svg>
          <span>www.belmontridge.com</span>
        </li>
      </ul>
    </div>
  </section>

  <section class="card card--back" aria-label="Business card back">
    <div class="back-pattern" role="img" aria-label="Embossed repeating brand-symbol pattern in navy and light blue"></div>
    <div class="back-brand"><span class="mark-square"></span><span>Belmont Ridge</span></div>
  </section>
</main>
</body>
</html>
```